Personal Injury Lawyer Billboard

I would like a design created featuring the image of the lawyer centered in the middle of the design.
To the left of the lawyer's image it should read "INJURED?"
To the right of the lawyer's image, it should read "CALL DEAN!"
Under Call Dean, include the phone number 318-555-0187.
At the bottom of the design include the lawyers information "Dean Marlowe Accident & Injury Lawyers"
PLEASE REMOVED THE BACKGROUND IMAGERY OF THE PHOTO SUBMITTED. Also, the colors for this design should match the colors shown in the logo (navy, white and relective soft gold). Please use those color combinations in ways that best stand out.

```html
<!DOCTYPE html>
<html lang="en">
<head>
<meta charset="UTF-8">
<title>Dean Marlowe Accident &amp; Injury Lawyers – Billboard</title>
<link href="https://fonts.googleapis.com/css2?family=Playfair+Display:wght@700;800;900&display=swap" rel="stylesheet">
<style>
  :root {
    --navy: #0b1f4d;
    --gold-deep: #d2b35e;
    --gold-light: #efe094;
    --gold-text: #ecd66f;
    --gold-rule: #c9a84a;
    --ink: #0a0a0a;
    --white: #ffffff;
    --page: #eceef1;
  }
  * { margin: 0; padding: 0; box-sizing: border-box; }
  html, body { width: 1200px; height: 1200px; overflow: hidden; background: var(--page); }
  .billboard {
    position: absolute;
    left: 40px; top: 380px;
    width: 1120px; height: 440px;
    overflow: hidden;
    background: linear-gradient(90deg, var(--gold-deep) 0%, var(--gold-light) 32%, var(--gold-light) 45%, var(--gold-deep) 75%, #d6b862 100%);
    font-family: "Playfair Display", Georgia, serif;
    font-variant-numeric: lining-nums;
  }
  .band-left {
    position: absolute; left: 0; top: 180px;
    width: 400px; height: 120px;
    background: var(--navy);
  }
  .band-right {
    position: absolute; left: 560px; top: 200px;
    width: 560px; height: 150px;
    background: var(--navy);
  }
  .headline-injured {
    position: absolute; left: 24px; top: 186px;
    z-index: 2;
    font-size: 96px; font-weight: 800; line-height: 110px;
    letter-spacing: -4px; color: var(--gold-text);
    transform: scaleX(0.76); transform-origin: left center;
    white-space: nowrap;
  }
  .lawyer-photo {
    position: absolute; left: 358px; top: 40px;
    width: 270px; height: 400px;
    border-radius: 120px 120px 0 0;
    background: linear-gradient(180deg, #b58a6c 0%, #a57b60 30%, #27336b 42%, #1c2a5e 100%);
  }
  .call-line {
    position: absolute; left: 622px; top: 14px;
    font-size: 94px; font-weight: 900; line-height: 104px;
    letter-spacing: -3px; color: var(--ink);
    transform: scaleX(0.8); transform-origin: left center;
    white-space: nowrap;
  }
  .call-line .name { color: var(--navy); }
  .phone {
    position: absolute; left: 612px; top: 100px;
    font-size: 92px; font-weight: 700; line-height: 100px;
    letter-spacing: -3px; color: var(--ink);
    transform: scaleX(0.82); transform-origin: left center;
    white-space: nowrap;
  }
  .firm {
    position: absolute; left: 670px; top: 220px;
    width: 370px; color: var(--white); text-align: center;
  }
  .firm-name {
    font-size: 50px; font-weight: 800; line-height: 58px;
    letter-spacing: -2px; white-space: nowrap;
    transform: scaleX(0.86);
  }
  .firm-tag {
    margin-top: 6px;
    border-top: 2px solid var(--gold-rule);
    border-bottom: 2px solid var(--gold-rule);
    font-size: 24px; font-weight: 700; line-height: 42px;
    letter-spacing: -0.5px; white-space: nowrap;
  }
</style>
</head>
<body>
  <main class="billboard">
    <div class="band-left"></div>
    <div class="band-right"></div>
    <div class="lawyer-photo" role="img" aria-label="Portrait of the lawyer in a navy suit and green tie, raising a fist, background removed"></div>
    <h1 class="headline-injured">INJURED?</h1>
    <p class="call-line">CALL <span class="name">DEAN!</span></p>
    <p class="phone">318-555-0187</p>
    <div class="firm">
      <p class="firm-name">DEAN MARLOWE</p>
      <p class="firm-tag">ACCIDENT &amp; INJURY LAWYERS</p>
    </div>
  </main>
</body>
</html>
```